Heron Property Inspection business card

I am the principal inspector of Heron Property Inspections. I serve Northern Virginia from Winchester to Arlington.Associate, Federated Guild of Dwelling Examiners (FGDE)Graduate, FGDE Home Inspectors CourseNational Association of Home Inspectors ExamI'd like the business card to look more professional than comical.I pulled the attached picture off the web. I'd like to have something like that or an image of a house as my logo on the cards.

Target Market(s)

Persons who recently purchased a home.

Industry/Entity Type

Business

Contact Information for Business Card

Bob AllenBadger Home Inspections, LLC.4455 River RoadBluemont, Virginia 20135cell: 703-231-6680e-mail: tkmarlow@postvale.net

Font styles to use
Serif
Sans Serif

Requirements
Must have
• I'd like to have a logo, something that identifies me as a home inspector. The attached images are something that I'd like to have incorporated into my business card logo.
Nice to have
• I'd like a sketch of a house and/or a magnifying glass showing a house being inspected. The attached images are used as a suggestion only, I do not own the images.
Should not have
• Gimmicky stuff. I want to appear professional and trustworthy.

```html
<!DOCTYPE html>
<html lang="en">
<head>
<meta charset="utf-8">
<title>Heron Property Inspections – Business Card</title>
<link href="https://fonts.googleapis.com/css2?family=Arimo:wght@400;700&display=swap" rel="stylesheet">
<style>
  :root {
    --page-bg: #e6e4e0;
    --card-top: #0b0f17;
    --card-mid: #1a2d52;
    --card-bottom: #2b559e;
    --brand-blue: #4f82d4;
    --text-light: #ffffff;
    --text-soft: #dbe4f3;
    --icon-ink: #111111;
  }
  * { margin: 0; padding: 0; box-sizing: border-box; }
  html, body {
    width: 1200px;
    height: 892px;
    overflow: hidden;
    background: var(--page-bg);
    font-family: "Arimo", Arial, sans-serif;
  }
  .canvas {
    width: 1200px;
    height: 892px;
    display: flex;
    align-items: center;
    justify-content: center;
  }
  .business-card {
    position: relative;
    width: 460px;
    height: 804px;
    border-radius: 30px;
    background: linear-gradient(180deg, var(--card-top) 0%, var(--card-mid) 45%, var(--card-bottom) 100%);
    box-shadow: 0 18px 40px rgba(0, 0, 0, 0.28);
    overflow: hidden;
    color: var(--text-light);
  }
  .brand {
    position: absolute;
    top: 150px;
    left: 0;
    right: 0;
    text-align: center;
    color: var(--brand-blue);
    font-weight: 700;
  }
  .brand-mark {
    display: block;
    width: 26px;
    height: 26px;
    border-radius: 50%;
    background: var(--brand-blue);
    margin: 0 auto 18px;
  }
  .brand-owner {
    font-size: 40px;
    line-height: 1.1;
    letter-spacing: 0.5px;
  }
  .brand-company {
    font-size: 27px;
    line-height: 1.3;
    margin-top: 6px;
  }
  .person {
    position: absolute;
    left: 44px;
    top: 480px;
  }
  .person-name {
    font-size: 34px;
    font-weight: 400;
  }
  .person-role {
    font-size: 18px;
    color: var(--text-soft);
    margin-top: 4px;
  }
  .contact {
    position: absolute;
    left: 44px;
    top: 590px;
    font-size: 22px;
    line-height: 1.25;
  }
  .contact-row {
    display: flex;
    align-items: center;
    gap: 14px;
    margin-bottom: 8px;
  }
  .contact-icon {
    width: 28px;
    height: 28px;
    background: var(--text-light);
    display: flex;
    align-items: center;
    justify-content: center;
    flex: none;
  }
  .contact-address {
    margin-top: 6px;
    font-size: 21px;
    line-height: 1.2;
  }
</style>
</head>
<body>
<main class="canvas">
  <article class="business-card">
    <header class="brand">
      <span class="brand-mark" aria-hidden="true"></span>
      <div class="brand-owner">Tim Marlow</div>
      <div class="brand-company">Heron Property Inspections, LLC</div>
    </header>

    <section class="person">
      <h1 class="person-name">Employee Name</h1>
      <p class="person-role">Your Position</p>
    </section>

    <section class="contact">
      <div class="contact-row">
        <span class="contact-icon" aria-hidden="true">
          <svg width="18" height="22" viewBox="0 0 18 22">
            <rect x="3" y="1" width="12" height="20" rx="2" fill="none" stroke="var(--icon-ink)" stroke-width="2"/>
            <rect x="6" y="4" width="6" height="5" fill="var(--icon-ink)"/>
            <circle cx="9" cy="16" r="1.6" fill="var(--icon-ink)"/>
          </svg>
        </span>
        <span>703-555-0192</span>
      </div>
      <div class="contact-row">
        <span class="contact-icon" aria-hidden="true">
          <svg width="22" height="16" viewBox="0 0 22 16">
            <rect x="1" y="1" width="20" height="14" fill="none" stroke="var(--icon-ink)" stroke-width="2"/>
            <path d="M1 1 L11 9 L21 1 M1 15 L8 7 M21 15 L14 7" fill="none" stroke="var(--icon-ink)" stroke-width="2"/>
          </svg>
        </span>
        <span>tkmarlow@postvale.net</span>
      </div>
      <address class="contact-address" style="font-style: normal;">
        7182 Quarry Lane Fernhill,<br>Virginia 20148
      </address>
    </section>
  </article>
</main>
</body>
</html>
```